Healthy Meal Delivery Website Needs to be updated, current, fresh and modern

Hi there,

The current website i have is super old and outdated.

I would like a beautiful modern site that has all the same content as the previous except with a a new, modern and trustworthy feel.

The current website is https://tovalplatefresh.com/

Target Market(s)

Health Conscious Young Professionals

Industry/Entity Type

Food Service

Font styles to use
Sans Serif

Requirements
Must have
• Modern Trustworthy feel
Should not have
• Anything out dated or cheesy or scammy

```html
<!DOCTYPE html>
<html lang="en">
<head>
<meta charset="utf-8">
<title>Toval Plate Fresh — Diet Meals Delivered</title>
<link rel="stylesheet" href="https://fonts.googleapis.com/css2?family=Open+Sans:wght@400;600;700&family=Roboto:wght@500;700;900&display=swap">
<style>
:root{
  --blue:#1b9fdc;
  --blue-deep:#0f7fc4;
  --green:#8cc63f;
  --ink:#2d2d2d;
  --muted:#555;
  --line:#e4e4e4;
  --star:#f3b71b;
  --flame:#f39a1e;
  --dark:#1d1b19;
  --paper:#fff;
  --mist:#f1f1f1;
}
*{margin:0;padding:0;box-sizing:border-box}
html,body{width:1200px;height:3879px;overflow:hidden;background:var(--paper)}
body{position:relative;font-family:"Open Sans",Arial,sans-serif;color:var(--ink)}
.abs{position:absolute}
h1,h2,h3{font-family:"Roboto",Arial,sans-serif}

/* header */
.site-header{left:0;top:0;width:1200px;height:135px;background:#fff}
.brand{left:116px;top:46px;display:flex;align-items:center;gap:12px;font-weight:700;font-size:24px;color:var(--blue)}
.brand-dot{width:30px;height:30px;border-radius:50%;background:var(--green)}
.phone{left:733px;top:34px;display:flex;align-items:center;gap:10px;font-size:20px;color:#333}
.login{left:918px;top:28px;width:165px;height:42px;background:var(--blue);color:#fff;font-size:14px;font-weight:700;display:flex;align-items:center;justify-content:center;gap:8px;border-radius:2px}
.nav{left:460px;top:94px;width:623px;display:flex;justify-content:space-between;font-size:13px;font-weight:600;color:#222}

/* hero */
.hero{left:0;top:135px;width:1200px;height:437px;background:linear-gradient(120deg,#3f4d38 0%,#6b8a3c 30%,#9e3a2a 55%,#4b6b2c 75%,#2d3a55 100%)}
.hero::after{content:"";position:absolute;inset:0;background:rgba(0,0,0,.28)}
.hero-copy{left:0;top:110px;width:1200px;text-align:center;color:#fff;z-index:2}
.hero-copy h1{font-size:58px;font-weight:700;line-height:64px;letter-spacing:.5px}
.hero-copy p{margin-top:14px;font-size:18px;font-weight:700;line-height:25px}
.slide-arrow{top:308px;width:42px;height:66px;background:#fff;display:flex;align-items:center;justify-content:center;z-index:2}

/* why */
.section-title{width:1200px;left:0;text-align:center;font-size:32px;font-weight:700;color:#333}
.section-lede{left:300px;width:600px;text-align:center;font-size:13px;line-height:26px;color:var(--muted)}
.feature{top:780px;width:240px;text-align:center}
.feature-ring{width:124px;height:124px;margin:0 auto;display:block}
.feature h3{margin-top:28px;font-size:17px;font-weight:700;color:var(--blue);letter-spacing:.5px}
.feature p{margin-top:8px;font-size:13px;line-height:20px;color:#444}
.feature .more{display:block;margin-top:12px;font-size:12px;font-weight:700;color:var(--blue)}
.chev{top:862px;font-size:26px;color:#222}

/* about */
.about{left:0;top:1112px;width:1200px;height:484px;background:linear-gradient(100deg,#0e86cf 0%,#1ea3e0 55%,#0a73bd 100%)}
.about h2{left:116px;top:92px;font-size:34px;color:#fff;font-weight:700}
.about-text{left:116px;top:150px;width:460px}
.about-text p{font-size:12px;line-height:21px;color:#fff}
.about-text p + p{margin-top:16px}
.btn-light{left:116px;top:341px;width:124px;height:44px;background:#21aee8;color:#fff;font-size:14px;font-weight:700;display:flex;align-items:center;justify-content:center;box-shadow:0 3px 6px rgba(0,0,0,.2)}
.about-photo{left:639px;top:70px;width:429px;height:383px;background:radial-gradient(ellipse at 50% 35%,#7a5a3a 0%,#4d6f2e 35%,#1e1e1e 62%,#dcdcdc 80%,#1a8fd3 100%)}

/* menu */
.menu-card{width:290px;height:352px;background:#fff;box-shadow:0 1px 6px rgba(0,0,0,.15)}
.menu-card .photo{height:165px}
.menu-card .body{padding:22px 24px}
.menu-card h3{font-family:"Open Sans",Arial,sans-serif;font-size:17px;font-weight:700;color:#222}
.rating{display:flex;align-items:center;gap:3px;margin-top:10px;font-size:13px;color:#333}
.rating i{width:16px;height:16px;background:var(--star);color:#fff;font-style:normal;font-size:12px;line-height:16px;text-align:center}
.rating span{margin-left:8px}
.menu-card .meta{margin-top:8px;font-size:12.5px;line-height:20px;color:#444}
.menu-card .maker{margin-top:8px;display:flex;align-items:center;gap:7px;font-size:13px;font-weight:600;color:var(--flame)}
.maker b{width:11px;height:11px;border-radius:50%;background:var(--flame)}
.btn-blue{left:538px;top:2617px;width:124px;height:52px;background:var(--blue);color:#fff;font-size:19px;font-weight:600;display:flex;align-items:center;justify-content:center}

/* testimonials */
.testimonials{left:0;top:2754px;width:1200px;height:409px;background:linear-gradient(180deg,#2a2623,#15130f 60%,#2c2a27)}
.testimonials h2{left:0;width:1200px;top:97px;text-align:center;color:#fff;font-size:32px}
.quote-mark{left:0;width:1200px;top:140px;text-align:center;color:#fff;font-size:44px;font-family:Georgia,serif;font-weight:700;line-height:1}
.avatar{width:88px;height:88px;border-radius:50%;border:3px solid #fff}
.review{width:360px;color:#fff;font-size:14px;line-height:22px}
.review strong{display:block;margin-top:14px;font-size:18px;font-family:"Roboto",Arial,sans-serif}

/* contact */
.contact-bg{left:0;top:3290px;width:1200px;height:589px;background:linear-gradient(180deg,#f4f4f4,#e9e9e9)}
.col-label{font-family:"Roboto",Arial,sans-serif;font-size:20px;font-weight:500;color:#222}
.map{left:116px;top:3445px;width:375px;height:274px;border:2px solid #222;background:linear-gradient(135deg,#c3d9b0,#e4e2d4 50%,#cfdcbc)}
.field{border:2px solid #222;background:transparent;font-size:12px;color:#555;padding:8px 10px}
.check{left:538px;top:3734px;display:flex;align-items:center;gap:6px;font-size:13px;color:#333}
.check b{width:13px;height:13px;border:1px solid #333;background:#fff;font-size:11px;line-height:11px;text-align:center;font-weight:700}
.submit{left:760px;top:3773px;width:96px;height:31px;border:2px solid #222;background:#fff;font-size:14px;font-weight:700;display:flex;align-items:center;justify-content:center}
.copy{left:0;width:1200px;top:3846px;text-align:center;font-size:11px;color:#555}
</style>
</head>
<body>

<header class="site-header abs">
  <div class="brand abs"><span class="brand-dot"></span>Toval Plate Fresh</div>
  <div class="phone abs">
    <svg width="18" height="18" viewBox="0 0 24 24"><path fill="#1b9fdc" d="M6.6 10.8a15 15 0 0 0 6.6 6.6l2.2-2.2a1 1 0 0 1 1-.25 11.4 11.4 0 0 0 3.6.57 1 1 0 0 1 1 1V20a1 1 0 0 1-1 1A17 17 0 0 1 3 4a1 1 0 0 1 1-1h3.5a1 1 0 0 1 1 1c0 1.25.2 2.45.57 3.57a1 1 0 0 1-.25 1z"/></svg>
    (416) 555-0182
  </div>
  <div class="login abs">
    <svg width="14" height="14" viewBox="0 0 24 24"><path fill="#fff" d="M10 17l5-5-5-5v3H2v4h8zM20 3h-8v2h8v14h-8v2h8a2 2 0 0 0 2-2V5a2 2 0 0 0-2-2z"/></svg>
    LOGIN /SIGN UP
  </div>
  <nav class="nav abs">
    <span>HOME</span><span>TOVAL MEAL PLANS</span><span>MENU</span><span>PRICING</span><span>ABOUT</span><span>PRESS</span><span>CONTACT</span><span>&#128722; MY CART ▾</span>
  </nav>
</header>

<section class="hero abs" role="img" aria-label="Fresh salad greens with strawberries and blackberries">
  <div class="hero-copy abs">
    <h1>THE TOVAL PLAN DELIVERS DIET<br>MEALS TO YOUR DOOR</h1>
    <p>Lorem Ipsum is simply dummy text of the printing and typesetting<br>industry. It has been the industry's standard dummy text</p>
  </div>
  <div class="slide-arrow abs" style="left:0"><svg width="14" height="22" viewBox="0 0 14 22"><path d="M11 2 3 11l8 9" stroke="#333" stroke-width="3" fill="none"/></svg></div>
  <div class="slide-arrow abs" style="right:0"><svg width="14" height="22" viewBox="0 0 14 22"><path d="m3 2 8 9-8 9" stroke="#333" stroke-width="3" fill="none"/></svg></div>
</section>

<section class="why">
  <h2 class="section-title abs" style="top:648px">WHY TOVAL PLATE MEALS</h2>
  <p class="section-lede abs" style="top:693px">Lorem Ipsum is simply dummy text of the printing and typesetting industry. Lorem Ipsum has been the industry's standard dummy text ever since the 1500s</p>
  <svg width="0" height="0" class="abs"><defs><linearGradient id="ring" x1="0" y1="0" x2="1" y2="1"><stop offset="0" stop-color="#c6d92b"/><stop offset="1" stop-color="#1b9fdc"/></linearGradient></defs></svg>

  <div class="feature abs" style="left:102px">
    <svg class="feature-ring" viewBox="0 0 124 124"><circle cx="62" cy="62" r="57" fill="#fff" stroke="url(#ring)" stroke-width="9"/><path d="M62 82 42 62a11 11 0 0 1 20-14 11 11 0 0 1 20 14z" fill="none" stroke="url(#ring)" stroke-width="6" stroke-linejoin="round"/></svg>
    <h3>HEALTHY</h3><p>Lorem Ipsum is simply dummy text<br>of the typesetting industry...</p><span class="more">Read More</span>
  </div>
  <div class="feature abs" style="left:356px">
    <svg class="feature-ring" viewBox="0 0 124 124"><circle cx="62" cy="62" r="57" fill="#fff" stroke="url(#ring)" stroke-width="9"/><rect x="42" y="44" width="36" height="36" rx="4" fill="none" stroke="url(#ring)" stroke-width="6"/><path d="m50 60 9 9 20-22" fill="none" stroke="url(#ring)" stroke-width="6"/></svg>
    <h3>CHOICE</h3><p>Lorem Ipsum is simply dummy text<br>of the typesetting industry.</p><span class="more">Read More</span>
  </div>
  <div class="feature abs" style="left:612px">
    <svg class="feature-ring" viewBox="0 0 124 124"><circle cx="62" cy="62" r="57" fill="#fff" stroke="url(#ring)" stroke-width="9"/><path d="M40 82c0-26 16-40 44-42 0 28-14 42-44 42zm4-4 26-24" fill="none" stroke="url(#ring)" stroke-width="6" stroke-linejoin="round"/></svg>
    <h3>FRESH</h3><p>Lorem Ipsum is simply dummy text<br>of the typesetting industry.</p><span class="more">Read More</span>
  </div>
  <div class="feature abs" style="left:865px">
    <svg class="feature-ring" viewBox="0 0 124 124"><circle cx="62" cy="62" r="57" fill="#fff" stroke="url(#ring)" stroke-width="9"/><circle cx="56" cy="66" r="13" fill="none" stroke="url(#ring)" stroke-width="8" stroke-dasharray="5 4"/><circle cx="56" cy="66" r="5" fill="url(#ring)"/><circle cx="76" cy="48" r="8" fill="none" stroke="url(#ring)" stroke-width="6" stroke-dasharray="4 3"/></svg>
    <h3>CUSTOMIZED</h3><p>Lorem Ipsum is simply dummy text<br>of the typesetting industry.</p><span class="more">Read More</span>
  </div>
  <span class="chev abs" style="left:74px">‹</span>
  <span class="chev abs" style="left:1133px">›</span>
</section>

<section class="about abs">
  <h2 class="abs">ABOUT US</h2>
  <div class="about-text abs">
    <p>Lorem Ipsum. Proin gravida nibh vel velit auctor aliquet. Aenean sollicitudin, ipsum, nec sagittis sem nibh id elit. Duis sed odio sit amet nibh vulputate cursus auctor a ornare odio. sed odio sit amet nibh vulputate cursus a sit amet mauris. Morbi accums an ipsum velit. Sed non mauris vitae erat.</p>
    <p>Lorem Ipsum. Proin gravida nibh vel velit auctor aliquet. Aenean sollicitudin, ipsum, nec sagittis sem nibh id elit. Duis sed odio sit amet nibh vulputate cursus auctor a ornare odio. sed odio sit amet nibh vulputate cursus a sit amet mauris.</p>
  </div>
  <div class="btn-light abs">READ MORE</div>
  <div class="about-photo abs" role="img" aria-label="Desktop computer screen showing a plate of roast beef with broccoli and tomato salad"></div>
</section>

<section class="menu">
  <h2 class="section-title abs" style="top:1678px">SELECT FROM OVER 100 MENU ITEMS</h2>
  <p class="section-lede abs" style="top:1738px;font-size:14px">Lorem Ipsum is simply dummy text of the printing and typesetting industry. It has been the industry's standard dummy text ever since the 1500s.</p>

  <article class="menu-card abs" style="left:150px;top:1831px">
    <div class="photo" role="img" aria-label="Stack of golden waffles" style="background:linear-gradient(135deg,#f3ece4,#b9773a 50%,#e9ddd0)"></div>
    <div class="body"><h3>Lorem Ipsum</h3><div class="rating"><i>★</i><i>★</i><i>★</i><i>★</i><i>★</i><span>36 reviews</span></div><p class="meta">Pizza, Italian<br>Break Fast, Toval Plate</p><div class="maker"><b></b>Toval Plate Fresh</div></div>
  </article>
  <article class="menu-card abs" style="left:455px;top:1831px">
    <div class="photo" role="img" aria-label="Salad with cucumber, onion and greens" style="background:linear-gradient(135deg,#7fa34a,#d9d3b5 50%,#5e8a35)"></div>
    <div class="body"><h3>Lorem Ipsum</h3><div class="rating"><i>★</i><i>★</i><i>★</i><i>★</i><i>★</i><span>36 reviews</span></div><p class="meta">Pizza, Italian<br>Lunch, Toval Plate</p><div class="maker"><b></b>Toval Plate Fresh</div></div>
  </article>
  <article class="menu-card abs" style="left:760px;top:1831px">
    <div class="photo" role="img" aria-label="Grilled steak with vegetables" style="background:linear-gradient(135deg,#3a2416,#8a4a24 50%,#d4862a)"></div>
    <div class="body"><h3>Lorem Ipsum</h3><div class="rating"><i>★</i><i>★</i><i>★</i><i>★</i><i>★</i><span>36 reviews</span></div><p class="meta">Pizza, Italian<br>Dinner, Toval Plate</p><div class="maker"><b></b>Toval Plate Fresh</div></div>
  </article>

  <article class="menu-card abs" style="left:150px;top:2237px">
    <div class="photo" role="img" aria-label="Yogurt cup topped with fresh fruit" style="background:linear-gradient(135deg,#f7eee8,#d8342e 45%,#f4f1ec)"></div>
    <div class="body"><h3>Lorem Ipsum</h3><div class="rating"><i>★</i><i>★</i><i>★</i><i>★</i><i>★</i><span>36 reviews</span></div><p class="meta">Pizza, Italian<br>Snacks, Toval Plate</p><div class="maker"><b></b>Toval Plate Fresh</div></div>
  </article>
  <article class="menu-card abs" style="left:455px;top:2237px">
    <div class="photo" role="img" aria-label="Seafood and vegetable stir fry" style="background:linear-gradient(135deg,#5a2a14,#c0542a 50%,#7a3a1a)"></div>
    <div class="body"><h3>Lorem Ipsum</h3><div class="rating"><i>★</i><i>★</i><i>★</i><i>★</i><i>★</i><span>36 reviews</span></div><p class="meta">Pizza, Italian<br>Dinner, Toval Plate</p><div class="maker"><b></b>Toval Plate Fresh</div></div>
  </article>
  <article class="menu-card abs" style="left:760px;top:2237px">
    <div class="photo" role="img" aria-label="Scrambled eggs with tomato" style="background:linear-gradient(135deg,#f5f1ea,#e8b83a 45%,#d5452a 70%,#f0ece6)"></div>
    <div class="body"><h3>Lorem Ipsum</h3><div class="rating"><i>★</i><i>★</i><i>★</i><i>★</i><i>★</i><span>36 reviews</span></div><p class="meta">Pizza, Italian<br>Break Fast, Toval Plate</p><div class="maker"><b></b>Toval Plate Fresh</div></div>
  </article>

  <div class="btn-blue abs">View All</div>
</section>

<section class="testimonials abs" role="img" aria-label="Dark dining table background">
  <h2 class="abs">TESTIMONIALS</h2>
  <div class="quote-mark abs">&ldquo;</div>
  <div class="avatar abs" role="img" aria-label="Customer portrait" style="left:119px;top:217px;background:linear-gradient(135deg,#8a7060,#4a3a30)"></div>
  <div class="review abs" style="left:246px;top:227px">&ldquo; Lorem ipsum dolor sit amet, consectetur adipisicing elit, sed do eiusmod tempor incididunt ut labore et<strong>Marcus Bell</strong></div>
  <div class="avatar abs" role="img" aria-label="Customer portrait" style="left:621px;top:217px;background:linear-gradient(135deg,#e6d6c8,#a88a6c)"></div>
  <div class="review abs" style="left:746px;top:227px">&ldquo; Lorem ipsum dolor sit amet, consectetur adipisicing elit, sed do eiusmod tempor incididunt ut labore et<strong>Lena Hart</strong></div>
</section>

<section class="contact">
  <div class="contact-bg abs"></div>
  <h2 class="section-title abs" style="top:3242px">GET IN TOUCH</h2>
  <p class="section-lede abs" style="top:3298px;left:260px;width:680px;font-size:12px;line-height:22px">Lorem ipsum madolor sit amet, consectetur adipisicing elit, sed do eiusmod tempor coli incididunt ut labore Lorem ipsum madolor sit amet, consectetur adipisicing incididunt.</p>
  <div class="col-label abs" style="left:246px;top:3400px">Map</div>
  <div class="col-label abs" style="left:724px;top:3400px">For Enquiry</div>
  <div class="map abs" role="img" aria-label="Map showing the kitchen location"></div>
  <div class="field abs" style="left:535px;top:3445px;width:261px;height:36px">Name</div>
  <div class="field abs" style="left:820px;top:3445px;width:261px;height:36px">E-mail</div>
  <div class="field abs" style="left:535px;top:3507px;width:546px;height:34px">Address</div>
  <div class="field abs" style="left:535px;top:3566px;width:546px;height:153px">Message</div>
  <div class="check abs"><b>✓</b>I'm Not a Robot</div>
  <div class="submit abs">Submit</div>
  <div class="copy abs">Copyright © 2018 . All Rights Reserved.</div>
</section>

</body>
</html>
```